BildeVOLD buisnesscard

Hey :) I need a modern buisnesscard for my company BildeVOLD
It most have:
Dagligleder og Fotograf: Henrik Audun Strandvik

Mob: +4791264085
Epost: post@bildevold.example
Adresse: Kvernbakken9, 6040 Fjordvik

Facbook and instagram logo with text BildeVOLD

BildeVOLD logo

It Company

```html
<!DOCTYPE html>
<html lang="no">
<head>
<meta charset="utf-8">
<title>BildeVOLD – visittkort</title>
<link rel="stylesheet" href="https://fonts.googleapis.com/css2?family=Khand:wght@600&family=Roboto:wght@400&display=swap">
<style>
  :root {
    --page: #e7e7e7;
    --card-dark: #0b0b0c;
    --card-light: #fbfbfb;
    --brand-blue: #1a74bb;
    --brand-pink: #d01a7d;
    --ink: #3d3d3d;
    --ink-soft: #4a4a4a;
    --white: #ffffff;
  }
  * { box-sizing: border-box; margin: 0; padding: 0; }
  html, body {
    width: 1200px; height: 576px; overflow: hidden;
    background: var(--page);
  }
  .sheet { position: relative; width: 1200px; height: 576px; }

  .card {
    position: absolute; top: 138px;
    width: 485px; height: 294px;
    box-shadow: 0 3px 8px rgba(0,0,0,.22);
    overflow: hidden;
  }
  .card--front { left: 81px; background: var(--card-dark); }
  .card--back  { left: 602px; background: var(--card-light); }

  .brand-mark { position: absolute; background: var(--brand-pink); }
  .brand-name {
    position: absolute;
    font-family: "Khand", sans-serif; font-weight: 600;
    color: var(--brand-blue); line-height: 1; white-space: nowrap;
    text-align: center;
  }

  .card--front .brand-mark { left: 206px; top: 94px; width: 72px; height: 72px; }
  .card--front .brand-name { left: 0; width: 100%; top: 172px; font-size: 42px; }

  .card--back .brand-mark { left: 353px; top: 32px; width: 62px; height: 62px; }
  .card--back .brand-name { left: 284px; width: 200px; top: 104px; font-size: 34px; }

  .person { position: absolute; left: 18px; top: 39px; }
  .person__name {
    font-family: "Khand", sans-serif; font-weight: 600;
    font-size: 23px; line-height: 1; color: var(--brand-blue);
  }
  .person__role {
    margin-top: 5px;
    font-family: "Roboto", sans-serif; font-size: 11.5px; color: var(--ink-soft);
  }

  .contact { position: absolute; left: 28px; top: 148px; list-style: none;
    font-family: "Roboto", sans-serif; font-size: 12.5px; color: var(--ink); }
  .contact li { display: flex; align-items: center; height: 17px; }
  .contact li.contact__social { margin-top: 6px; }
  .contact svg { width: 11px; height: 11px; margin-right: 7px; flex: none; }
  .social-square { width: 10px; height: 10px; background: var(--brand-pink); margin-right: 5px; flex: none; }

  .waves { position: absolute; left: 0; top: 0; width: 485px; height: 294px; }
  .website {
    position: absolute; left: 300px; top: 243px; width: 170px; text-align: right;
    font-family: "Roboto", sans-serif; font-size: 12px; color: var(--white);
  }
</style>
</head>
<body>
<main class="sheet">
  <section class="card card--front" aria-label="Forside">
    <span class="brand-mark"></span>
    <span class="brand-name">BildeVOLD</span>
  </section>

  <section class="card card--back" aria-label="Bakside">
    <svg class="waves" viewBox="0 0 485 294" aria-hidden="true">
      <path fill="var(--brand-blue)" d="M0,294 L0,284 C120,292 250,272 340,228 C392,203 440,188 485,184 L485,294 Z"/>
      <path fill="var(--brand-pink)" d="M0,246 C60,262 140,269 210,263 C300,255 380,212 485,174 L485,181 C390,210 300,268 205,279 C125,286 55,276 0,266 Z"/>
      <path fill="none" stroke="var(--brand-pink)" stroke-width="2.5" d="M60,262 C190,270 300,248 420,196"/>
    </svg>

    <span class="brand-mark"></span>
    <span class="brand-name">BildeVOLD</span>

    <div class="person">
      <p class="person__name">Henrik Audun Strandvik</p>
      <p class="person__role">Managing Director &amp; Photographer</p>
    </div>

    <ul class="contact">
      <li>
        <svg viewBox="0 0 12 12"><rect x="3" y="0.5" width="6" height="11" rx="1.2" fill="none" stroke="var(--brand-blue)" stroke-width="1.4"/><rect x="5" y="9" width="2" height="1" fill="var(--brand-blue)"/></svg>
        +4791264085
      </li>
      <li>
        <svg viewBox="0 0 12 12"><rect x="0.5" y="2" width="11" height="8" fill="var(--brand-blue)"/><path d="M1,2.5 L6,7 L11,2.5" fill="none" stroke="var(--white)" stroke-width="1"/></svg>
        post@bildevold.example
      </li>
      <li>
        <svg viewBox="0 0 12 12"><path d="M6,0.5 C3.5,0.5 2,2.3 2,4.4 C2,7 6,11.5 6,11.5 C6,11.5 10,7 10,4.4 C10,2.3 8.5,0.5 6,0.5 Z" fill="var(--brand-blue)"/><circle cx="6" cy="4.4" r="1.5" fill="var(--white)"/></svg>
        Kvernbakken9, 6040 Fjordvik
      </li>
      <li class="contact__social">
        <span class="social-square"></span>
        /BildeVOLD
      </li>
    </ul>

    <p class="website">www.bildevold.example</p>
  </section>
</main>
</body>
</html>
```